High-end construction company needs a business card design

We need a modern looking business card that draws people in, is memorable and looks so good people will want to sick it on their fridges.
On the first side what is needed are:
Logo
My name - Tomasz Brelwik
Title - Managing Director
Website - www.varkelt.co.uk
Email - tomasz@varkelt.co.uk
Telephone - 020 5194 6281
Mobile - 07845139072
On the back side was is needed is a list of all the services we provide:
-Kitchen Renovations
-Bathroom Renovations
-House Renovations
-Garage Conversions
-Extensions
-Loft Conversions
-Conservatories
-Carpentry
-Tiling
-Electrical
-Plumbing & Heating
-Bricklaying
-Landscaping
-Decorating
-Plastering
We would like the colours to be the same shades as on the logo with grey or black for the words.
Target Market(s)
Anyone who needs building work done
Contact Information for Business Card
This business card is for a construction company which strives to deliver excellent service and quality.
The look and feel of the card should represent this.
Requirements
Must have
- On the first side what is needed are:
Logo
My name - Tomasz Brelwik
Title - Managing Director
Website - www.varkelt.co.uk
Email - tomasz@varkelt.co.uk
Telephone - 020 5194 6281
Mobile - 07845139072
Nice to have
- Cool looking features

```html
<!DOCTYPE html>
<html lang="en">
<head>
<meta charset="utf-8">
<title>Varkelt Construction Ltd – Business Card</title>
<link rel="stylesheet" href="https://fonts.googleapis.com/css2?family=Poppins:wght@400;500;700&display=swap">
<style>
  :root {
    --bg: #d9d9d6;
    --card: #2f2f31;
    --card-edge: #5fb832;
    --green: #6cc13b;
    --green-dark: #3f8f2c;
    --text: #f2f2f2;
  }
  * { box-sizing: border-box; margin: 0; padding: 0; }
  html, body {
    width: 1200px; height: 795px; overflow: hidden;
    background: var(--bg);
    font-family: "Poppins", sans-serif;
  }
  .stage {
    position: relative; width: 1200px; height: 795px;
    display: flex; align-items: center; justify-content: center; gap: 28px;
  }
  .card {
    position: relative; width: 560px; height: 320px;
    background: var(--card);
    border-bottom: 3px solid var(--card-edge);
    border-left: 2px solid var(--card-edge);
    box-shadow: 0 10px 24px rgba(0,0,0,.25);
    overflow: hidden;
  }

  /* Back side: services */
  .services { position: absolute; left: 34px; top: 26px; }
  .services__title {
    color: var(--green); font-weight: 700; font-size: 15px; letter-spacing: .5px;
    margin-bottom: 4px;
  }
  .services__list { list-style: none; }
  .services__list li {
    color: var(--text); font-size: 11px; line-height: 16px; padding-left: 10px; position: relative;
  }
  .services__list li::before {
    content: ""; position: absolute; left: 0; top: 6px;
    width: 4px; height: 4px; border-radius: 50%; background: var(--green);
  }

  .brand { position: absolute; color: var(--green); font-weight: 700; line-height: 1; }
  .brand--back { right: 36px; bottom: 40px; text-align: right; }
  .brand--front { right: 44px; top: 66px; text-align: right; }
  .brand__name { display: block; font-size: 58px; letter-spacing: 1px; }
  .brand__sub { display: block; font-size: 15px; letter-spacing: 3.5px; margin-top: 6px; }
  .brand--front .brand__name { font-size: 48px; }
  .brand--front .brand__sub { font-size: 12.5px; letter-spacing: 3px; }

  /* Front side */
  .person { position: absolute; left: 40px; top: 100px; }
  .person__name { color: var(--green); font-weight: 700; font-size: 20px; line-height: 26px; letter-spacing: .5px; text-transform: uppercase; }
  .person__title { color: var(--text); font-size: 14px; line-height: 20px; }
  .divider {
    position: absolute; left: 40px; right: 44px; top: 168px;
    height: 1.5px; background: var(--green-dark);
  }
  .contact { position: absolute; left: 40px; top: 178px; list-style: none; }
  .contact li {
    display: flex; align-items: center; gap: 8px;
    color: var(--text); font-size: 15px; line-height: 24px;
  }
  .contact svg { width: 13px; height: 13px; fill: var(--green); flex: none; }
  .address {
    position: absolute; right: 44px; bottom: 30px; text-align: right;
    color: var(--text); font-size: 16px; line-height: 22px; font-style: normal;
  }
</style>
</head>
<body>
<main class="stage">

  <section class="card card--back" aria-label="Card back: services">
    <div class="services">
      <h2 class="services__title">SERVICES</h2>
      <ul class="services__list">
        <li>Kitchen Renovations</li>
        <li>Bathroom Renovations</li>
        <li>House Renovations</li>
        <li>Garage Conversions</li>
        <li>Extensions</li>
        <li>Loft Conversions</li>
        <li>Conservatories</li>
        <li>Carpentry</li>
        <li>Tiling</li>
        <li>Electrical</li>
        <li>Plumbing &amp; Heating</li>
        <li>Bricklaying</li>
        <li>Landscaping</li>
        <li>Decorating</li>
        <li>Plastering</li>
      </ul>
    </div>
    <div class="brand brand--back">
      <span class="brand__name">VARKELT</span>
      <span class="brand__sub">CONSTRUCTION LTD</span>
    </div>
  </section>

  <section class="card card--front" aria-label="Card front: contact details">
    <div class="person">
      <h1 class="person__name">Tomasz Brelwik</h1>
      <p class="person__title">Managing Director</p>
    </div>
    <div class="brand brand--front">
      <span class="brand__name">VARKELT</span>
      <span class="brand__sub">CONSTRUCTION LTD</span>
    </div>
    <div class="divider"></div>
    <ul class="contact">
      <li><svg viewBox="0 0 24 24"><path d="M6.6 10.8a15.1 15.1 0 0 0 6.6 6.6l2.2-2.2c.3-.3.7-.4 1-.2 1.1.4 2.3.6 3.6.6.6 0 1 .4 1 1V20c0 .6-.4 1-1 1A17 17 0 0 1 3 4c0-.6.4-1 1-1h3.5c.6 0 1 .4 1 1 0 1.3.2 2.5.6 3.6.1.3 0 .7-.2 1z"/></svg>020 5194 6281</li>
      <li><svg viewBox="0 0 24 24"><path d="M7 1h10a2 2 0 0 1 2 2v18a2 2 0 0 1-2 2H7a2 2 0 0 1-2-2V3a2 2 0 0 1 2-2zm0 3v14h10V4zm5 15.5a1 1 0 1 0 0 2 1 1 0 0 0 0-2z"/></svg>07845139072</li>
      <li><svg viewBox="0 0 24 24"><path d="M2 5h20v14H2zm2 2v.5l8 5 8-5V7zm0 2.8V17h16V9.8l-8 5z"/></svg>tomasz@varkelt.co.uk</li>
      <li><svg viewBox="0 0 24 24"><path d="M12 2a10 10 0 1 0 0 20 10 10 0 0 0 0-20zm6.9 9h-3a15 15 0 0 0-1.3-5.9A8 8 0 0 1 18.9 11zM12 4c.9 1.2 1.8 3.6 1.9 7h-3.8c.1-3.4 1-5.8 1.9-7zM9.4 5.1A15 15 0 0 0 8.1 11h-3a8 8 0 0 1 4.3-5.9zM5.1 13h3a15 15 0 0 0 1.3 5.9A8 8 0 0 1 5.1 13zm6.9 7c-.9-1.2-1.8-3.6-1.9-7h3.8c-.1 3.4-1 5.8-1.9 7zm2.6-1.1a15 15 0 0 0 1.3-5.9h3a8 8 0 0 1-4.3 5.9z"/></svg>www.varkelt.co.uk</li>
    </ul>
    <address class="address">48 Harrow Lane<br>London, E9 4QT</address>
  </section>

</main>
</body>
</html>
```